'Horizons on Common Ground'

We are after a flyer to sell a two day conference to sponsors, delegates and other Councils to participate.
The conference aims to be a forum for Northern Territory Councils to get together and discuss ideas, issues and overcome challenges and isolation in collaboration.
The conference will be a inaugural event with the plan to host a annual two day conference each year with a specific theme relevant to all Northern Territory Councils. - Give the Councils a voice.

```html
<!DOCTYPE html>
<html lang="en">
<head>
<meta charset="utf-8">
<title>Horizons on Common Ground</title>
<link rel="stylesheet" href="https://fonts.googleapis.com/css2?family=Arimo:ital,wght@0,400;0,700;1,400;1,700&display=swap">
<style>
  :root {
    --silver-light: #f4f4f4;
    --silver-mid: #c9c9c9;
    --silver-dark: #8e8e8e;
    --ink: #111111;
    --white: #ffffff;
    --band-dark: #1c1c1c;
    --band-stripe: #4a4a4a;
    --sea-deep: #2a8fa8;
    --sea-light: #7fd6dc;
    --sky: #c9d7df;
    --hill-green: #4f6b3a;
    --hill-dark: #25331d;
  }
  * { margin: 0; padding: 0; box-sizing: border-box; }
  html, body { width: 849px; height: 1200px; overflow: hidden; }
  body { font-family: "Arimo", Arial, sans-serif; }

  .flyer {
    position: relative;
    width: 849px;
    height: 1200px;
    overflow: hidden;
    background: linear-gradient(135deg, var(--silver-light) 0%, var(--silver-mid) 55%, var(--silver-dark) 100%);
  }

  .coast-photo {
    position: absolute;
    left: 435px; top: 0;
    width: 414px; height: 470px;
    background: linear-gradient(175deg, var(--sky) 0%, #8ea89a 22%, var(--sea-light) 40%, var(--sea-deep) 100%);
  }

  .hills-photo {
    position: absolute;
    left: 0; top: 688px;
    width: 418px; height: 512px;
    background: linear-gradient(160deg, #9fb0a8 0%, var(--hill-green) 30%, var(--hill-dark) 100%);
  }

  .stripe-band {
    position: absolute;
    left: 0; top: 450px;
    width: 849px; height: 238px;
    background:
      repeating-linear-gradient(180deg, var(--band-stripe) 0 2px, var(--band-dark) 2px 5px),
      var(--band-dark);
    box-shadow: 0 0 6px rgba(0,0,0,0.5);
  }
  .stripe-band::before {
    content: "";
    position: absolute; inset: 0;
    background: linear-gradient(90deg, rgba(255,255,255,0.15), rgba(0,0,0,0.2) 50%, rgba(255,255,255,0.1));
  }

  .swirl-disc {
    position: absolute;
    left: 248px; top: 378px;
    width: 384px; height: 384px;
    border-radius: 50%;
    border: 8px solid #d8d8d8;
    background:
      radial-gradient(circle at 62% 40%, rgba(255,255,255,0.75) 0%, rgba(200,200,200,0.35) 30%, rgba(20,20,20,0) 60%),
      repeating-linear-gradient(180deg, #3d3d3d 0 2px, #151515 2px 5px);
    box-shadow: 0 0 10px rgba(0,0,0,0.55);
  }

  .title-block { position: absolute; left: 35px; top: 82px; }
  .event-name {
    color: var(--white);
    font-weight: 700;
    font-style: italic;
    text-transform: uppercase;
    line-height: 0.95;
    text-shadow: 0 0 3px rgba(0,0,0,0.15);
  }
  .event-name .big { display: block; font-size: 62px; }
  .event-name .small { display: block; font-size: 39px; margin-top: 10px; }
  .title-rule {
    width: 350px; height: 2px;
    background: var(--white);
    margin: 14px 0 14px;
  }
  .event-date {
    color: var(--ink);
    font-weight: 400;
    font-size: 54px;
    line-height: 1.08;
  }
  .event-date .month { display: block; font-style: italic; }

  .vision-block {
    position: absolute;
    left: 35px; top: 884px;
    width: 370px;
    color: var(--white);
    font-style: italic;
    text-transform: uppercase;
  }
  .vision-block h2 { font-size: 27px; font-weight: 700; line-height: 1.1; }
  .vision-block p { font-size: 12.5px; font-weight: 700; line-height: 1.1; margin-top: 4px; }
  .vision-block h2.objective { margin-top: 24px; }

  .core-values {
    position: absolute;
    left: 428px; top: 798px;
    width: 380px;
    color: var(--ink);
    font-style: italic;
  }
  .core-values h3 { font-size: 15px; font-weight: 400; text-transform: uppercase; line-height: 1.15; }
  .core-values p { font-size: 12.5px; line-height: 1.22; margin-bottom: 2px; }
</style>
</head>
<body>
<main class="flyer">
  <div class="coast-photo" role="img" aria-label="Aerial photograph of a tropical coastline with turquoise reef water"></div>
  <div class="hills-photo" role="img" aria-label="Photograph of green coastal hills above a seaside town"></div>
  <div class="stripe-band"></div>
  <div class="swirl-disc" role="img" aria-label="Abstract white light swirl on dark horizontal lines"></div>

  <header class="title-block">
    <h1 class="event-name">
      <span class="big">Horizons</span>
      <span class="big">On</span>
      <span class="small">Common Ground</span>
    </h1>
    <div class="title-rule"></div>
    <p class="event-date">13th-14th<span class="month">April 2011</span></p>
  </header>

  <section class="vision-block">
    <h2>Vision &amp; Mission</h2>
    <p>A region whose people are healthy<br>happy and positive about their future.</p>
    <h2 class="objective">Objective</h2>
    <p>A strong, reliable and responsible shire council that will support the people of Coral Ridge by providing a range of high quality services that lead to community, cultural, economic and environmental wellbeing.</p>
  </section>

  <section class="core-values">
    <h3>Core Values</h3>
    <p>We have identified these key values and principles<br>as integral to the achievement of our vision.</p>
    <h3>Respect</h3>
    <p>Acknowledge and value individual community identity indigenous culture and heritage, in an environment free of discrimination.</p>
    <h3>Professionalism</h3>
    <p>Administration, planning, logistics, communications and governance of the highest standard.</p>
    <h3>Results</h3>
    <p>Achievement of agreed service delivery standards.</p>
    <h3>Integrity</h3>
    <p>Dealing honestly and fairly with all stakeholders.</p>
    <h3>Innovation</h3>
    <p>Developing new ways of delivering services and<br>solving implementation problems.</p>
    <h3>Engagement</h3>
    <p>Listen effectively to residents and ratepayers and<br>collaborate with Stakeholders.</p>
  </section>
</main>
</body>
</html>
```